Keepsakes of Mine trifold brochure design

We are a start up company that will help seniors write their memoirs...beginning with a few ancestors and their heritage and continuing through their own history...how they would like to be remembered in the next generation. I envision a senior citizen at an older writing desk, writing her memoirs, with a book (maybe standing on top, leaning slightly) that has the words Keepsakes of Mine.com on the back binding. OR maybe a senior couple walking into the sunset with the same book somewhere in the frame. Communicating the relevance of every life being significant to those that come after them...when a genealogy doesn't say enough about the details of one's life. Please note that I am open to the professionals own ideas...I am not locked into my concepts. I would like one or two phrases..."When A Genealogy Doesn't Say Enough" and/or "Every life legacy is a gift for the next generation to treasure" to be in the design.
A few documents are loaded that contain notes for our web designers. Maybe they will help you with our thoughts.
Updates

Reason: We have added some additional photos that might be useful.

Target Market(s)

Seniors and the baby boomer generation

Industry/Entity Type

Graphic Design

Requirements
Must have
• Keepsakes of Mine
• Doris Whitcombe, M.A.
• 1-555-218-6470 (local)
• 1-855-7RELICS (toll free)
• info@keepsakesofmine.example
• keepsakesofmine.example
Should not have
• Scripts that would be challenging for seniors to read.

```html
<!DOCTYPE html>
<html lang="en">
<head>
<meta charset="utf-8">
<title>Keepsakes of Mine – Trifold Brochure</title>
<link href="https://fonts.googleapis.com/css2?family=Open+Sans:wght@400;600&display=swap" rel="stylesheet">
<style>
  :root {
    --page-bg: #ececec;
    --panel-dark: #3a2328;
    --panel-mid: #5a3a32;
    --band-tan: #8a6a58;
    --photo-warm: #a0684a;
    --photo-deep: #4a2a22;
    --gold: #b8914a;
    --gold-soft: #c9a878;
    --gold-line: rgba(196, 160, 110, 0.55);
    --label-white: #f7f5f2;
  }
  html, body {
    margin: 0;
    width: 1200px;
    height: 794px;
    overflow: hidden;
    background: var(--page-bg);
    font-family: "Open Sans", sans-serif;
  }
  .spread {
    position: absolute;
    top: 47px;
    left: 50%;
    transform: translateX(-50%);
    display: flex;
    gap: 40px;
  }
  .panel {
    position: relative;
    width: 300px;
    height: 700px;
    box-shadow: 0 6px 18px rgba(0,0,0,0.18);
    overflow: hidden;
  }
  .panel-frame {
    position: absolute;
    inset: 12px;
    border: 1px solid var(--gold-line);
    border-radius: 4px;
    pointer-events: none;
  }
  .brand-name {
    margin: 0;
    font-weight: 600;
    font-size: 22px;
    line-height: 1.2;
    color: var(--gold);
    letter-spacing: 0.3px;
    white-space: nowrap;
    text-align: center;
  }

  /* Back panel */
  .back-panel { background: var(--panel-dark); }
  .back-logo-box {
    position: absolute;
    top: 42px;
    left: 28px;
    right: 28px;
    height: 170px;
    border: 1px solid var(--gold-line);
    display: flex;
    align-items: center;
    justify-content: center;
  }
  .back-message {
    position: absolute;
    top: 250px;
    left: 32px;
    right: 32px;
    text-align: center;
    color: var(--gold-soft);
  }
  .back-heading {
    margin: 0 0 14px;
    font-weight: 600;
    font-size: 17px;
    line-height: 1.35;
    color: var(--gold);
  }
  .back-quote {
    margin: 0;
    font-size: 14px;
    line-height: 1.5;
  }
  .contact {
    position: absolute;
    bottom: 42px;
    left: 32px;
    right: 32px;
    margin: 0;
    text-align: center;
    font-style: normal;
    font-size: 13px;
    line-height: 1.7;
    color: var(--gold-soft);
  }
  .contact-name {
    display: block;
    font-weight: 600;
    font-size: 15px;
    color: var(--gold);
    margin-bottom: 4px;
  }
  .contact-rule {
    width: 60px;
    height: 1px;
    margin: 0 auto 16px;
    background: var(--gold-line);
  }

  /* Cover panel */
  .cover-panel {
    background: linear-gradient(180deg, var(--band-tan) 0%, var(--panel-mid) 28%, var(--panel-dark) 100%);
  }
  .cover-photo {
    position: absolute;
    top: 150px;
    left: 0;
    right: 0;
    height: 400px;
    background:
      radial-gradient(ellipse at 25% 70%, rgba(240,170,90,0.55) 0%, rgba(240,170,90,0) 35%),
      linear-gradient(160deg, var(--photo-warm) 0%, #7a4a36 45%, var(--photo-deep) 100%);
    -webkit-mask-image: linear-gradient(180deg, transparent 0%, #000 12%, #000 80%, transparent 100%);
    mask-image: linear-gradient(180deg, transparent 0%, #000 12%, #000 80%, transparent 100%);
  }
  .cover-label {
    position: absolute;
    top: 30px;
    left: 34px;
    right: 34px;
    height: 150px;
    box-sizing: border-box;
    padding: 0 12px;
    background: var(--label-white);
    border-radius: 10px;
    display: flex;
    align-items: center;
    justify-content: center;
    box-shadow: 0 2px 6px rgba(0,0,0,0.2);
  }
  .cover-tagline {
    position: absolute;
    bottom: 40px;
    left: 0;
    right: 0;
    margin: 0;
    text-align: center;
    white-space: nowrap;
    font-weight: 600;
    font-size: 18px;
    color: var(--gold);
  }
</style>
</head>
<body>
  <main class="spread">
    <section class="panel back-panel" aria-label="Back panel">
      <div class="panel-frame"></div>
      <div class="back-logo-box">
        <p class="brand-name">Keepsakes of Mine</p>
      </div>
      <div class="back-message">
        <p class="back-heading">When A Genealogy Doesn't Say Enough</p>
        <p class="back-quote">Every life legacy is a gift for the next generation to treasure.</p>
      </div>
      <address class="contact">
        <div class="contact-rule"></div>
        <span class="contact-name">Doris Whitcombe, M.A.</span>
        1-555-218-6470 (local)<br>
        1-855-7RELICS (toll free)<br>
        info@keepsakesofmine.example<br>
        keepsakesofmine.example
      </address>
    </section>

    <section class="panel cover-panel" aria-label="Front cover">
      <div class="cover-photo" role="img" aria-label="Photograph of a senior woman writing her memoirs at an old wooden writing desk by lamplight"></div>
      <div class="panel-frame"></div>
      <div class="cover-label">
        <p class="brand-name">Keepsakes of Mine</p>
      </div>
      <p class="cover-tagline">Encouragement for the Believer</p>
    </section>
  </main>
</body>
</html>
```